CLEARLINE™ by VESKO GOLF Squarespace website design

I am looking to have the website look and feel designed. I will attach all the initial content and some other sites I like for inspiration. https://www.fairwaysensa.com/ https://quillstrike.com/
This is the top bar nav
CLEARLINE™ by VESKO GOLF logo
Center: Home | Process | Technology | The Fit | Stroke Print | Testimonials | About
Right: [Start My Fitting] (gold CTA button)

Target Market(s)

Upscale Golfers

Industry/Entity Type

Golf and Technology

```html
<!DOCTYPE html>
<html lang="en">
<head>
<meta charset="utf-8">
<title>CLEARLINE™ by VESKO GOLF</title>
<link rel="stylesheet" href="https://fonts.googleapis.com/css2?family=Montserrat:ital,wght@0,400;0,500;0,600;0,700;0,800;0,900;1,400&display=swap">
<style>
:root{
  --gold:#ffd400;
  --ink:#111111;
  --dark:#222222;
  --dark-2:#2b2b2b;
  --card:#0c0c0c;
  --white:#ffffff;
  --muted:#d6d6d6;
  --line:#555555;
}
*{box-sizing:border-box;margin:0;padding:0}
html,body{width:1200px;height:3406px;overflow:hidden;background:var(--dark);font-family:'Montserrat',sans-serif;color:var(--white)}
section,header,footer{position:relative;width:1200px}
.btn{display:inline-block;background:var(--gold);color:var(--ink);font-weight:700;font-size:14px;padding:12px 20px;text-decoration:none}
.btn-outline{display:inline-block;border:1.5px solid var(--white);color:var(--white);font-weight:700;font-size:14px;padding:12px 38px;text-decoration:none}
.gold{color:var(--gold)}

/* hero */
.hero{height:652px;background:linear-gradient(90deg,#0f1410 0%,#1a2418 40%,#3d5a2c 62%,#6f8f3a 78%,#2c3a22 100%)}
.hero-photo{position:absolute;inset:0;background:radial-gradient(ellipse at 80% 35%,rgba(255,220,120,.45),transparent 35%),linear-gradient(90deg,rgba(10,12,10,.85) 0%,rgba(10,12,10,.55) 45%,rgba(0,0,0,0) 60%)}
.nav{position:absolute;top:0;left:0;width:1200px;height:92px;background:rgba(10,10,10,.6);display:flex;align-items:center;padding:0 75px}
.logo{display:flex;flex-direction:column;line-height:1}
.logo-name{font-weight:700;font-size:20px;letter-spacing:.5px;color:var(--white)}
.logo-sub{font-weight:500;font-size:8px;letter-spacing:4px;color:#9a9a9a;margin-top:4px}
.nav-links{display:flex;gap:29px;margin-left:110px;font-size:13px;font-weight:500}
.nav-links a{color:var(--white);text-decoration:none}
.nav-links a.active{color:var(--gold)}
.nav .btn{margin-left:auto;font-size:14px;padding:12px 18px}
.hero-copy{position:absolute;left:75px;top:232px;width:520px}
.hero-copy h1{font-size:46px;font-weight:900;line-height:1.1;letter-spacing:1px}
.hero-copy p{margin-top:26px;font-size:15px;line-height:1.55;font-weight:500}
.hero-copy .btn{margin-top:26px}

/* welcome */
.welcome{height:518px;background:var(--dark)}
.welcome-media{position:absolute;left:75px;top:70px;width:514px;height:370px;border-radius:14px;background:linear-gradient(135deg,#2d4a2a,#6a8a3c 45%,#c9b23a 60%,#2f4a30)}
.welcome-copy{position:absolute;left:615px;top:60px;width:520px}
.welcome-copy h2{font-size:36px;font-weight:600;line-height:1.2}
.welcome-copy h2 span{font-size:32px;font-weight:500}
.welcome-copy p{margin-top:20px;font-size:14px;line-height:1.6;color:var(--muted)}
.welcome-copy .btn{margin-top:26px}
.welcome-copy small{display:block;margin-top:24px;font-size:11.5px;color:var(--muted)}

/* why */
.why{height:410px;background:var(--dark-2);text-align:center}
.why h2{padding-top:44px;font-size:36px;font-weight:600}
.why .sub{margin-top:12px;font-size:11.5px;color:var(--muted)}
.why-grid{position:absolute;top:168px;left:75px;width:1050px;display:grid;grid-template-columns:repeat(4,1fr)}
.why-icon{width:54px;height:54px;margin:0 auto;border:2px solid #bdbdbd;border-radius:12px}
.why-item.featured .why-icon{border-color:var(--gold)}
.why-item h3{margin-top:18px;font-size:18px;font-weight:600;line-height:1.25}
.why-item.featured h3{color:var(--gold)}
.why-item p{margin-top:12px;font-size:14px;line-height:1.7;color:var(--muted)}

/* how */
.how{height:853px;background:linear-gradient(180deg,var(--dark) 0 360px,var(--gold) 360px)}
.how-card{position:absolute;left:75px;top:70px;width:1051px;height:475px;background:var(--card);border-radius:14px}
.how-card h2{position:absolute;left:32px;top:50px;font-size:36px;font-weight:700}
.steps{position:absolute;left:32px;top:116px;width:360px}
.step{display:flex;gap:18px;margin-bottom:28px}
.step-num{font-size:36px;font-weight:600;color:#d9d9d9;width:34px;line-height:1}
.step h3{font-size:18px;font-weight:600;color:var(--gold)}
.step p{margin-top:4px;font-size:13px;line-height:1.6;color:var(--muted)}
.how-card .btn-outline{position:absolute;left:32px;top:374px}
.how-media{position:absolute;left:450px;top:37px;width:571px;height:401px;border-radius:12px;background:linear-gradient(120deg,#3e5a3a,#6d8a52 45%,#2a3a30 75%,#141a18)}
.stat{position:absolute;top:612px;left:0;width:1200px;text-align:center;color:var(--ink)}
.stat h2{font-size:37px;font-weight:700;line-height:1.2}
.stat p{margin:24px auto 0;width:860px;font-size:18px;line-height:1.5}

/* proof */
.proof{height:486px;background:var(--dark)}
.proof h2{position:absolute;left:73px;top:64px;font-size:37px;font-weight:700;line-height:1.2}
.proof-lede{position:absolute;left:343px;top:78px;font-size:18px;line-height:1.5;color:var(--muted)}
.proof-arrows{position:absolute;left:1064px;top:103px;display:flex;gap:13px}
.quotes{position:absolute;left:75px;top:192px;width:1051px;display:grid;grid-template-columns:repeat(3,1fr)}
.quote{padding:0 32px 0 0}
.quote + .quote{border-left:1px solid var(--line);padding-left:34px}
.quote blockquote{font-size:18.5px;font-style:italic;line-height:1.7;color:#e6e6e6}
.quote cite{display:block;margin-top:16px;font-style:normal;font-weight:700;font-size:15px}
.proof .btn-outline{position:absolute;left:501px;top:386px;border-color:#cfcfcf;padding:12px 38px}

/* cta */
.cta{height:307px;background:linear-gradient(90deg,#1c2519,#2c3b24 50%,#233023);text-align:center}
.cta-overlay{position:absolute;inset:0;background:rgba(0,0,0,.45)}
.cta-copy{position:absolute;top:82px;left:0;width:1200px}
.cta-copy h2{font-size:35px;font-weight:700;line-height:1.25}
.cta-copy .btn{margin-top:20px}

/* footer */
.footer{height:180px;background:var(--dark)}
.footer .copy{position:absolute;left:75px;top:82px;font-size:12px;color:var(--muted)}
.footer .logo{position:absolute;left:514px;top:70px;align-items:center}
.footer .tag{position:absolute;left:0;width:1200px;top:140px;text-align:center;font-size:14px;color:var(--gold)}
.social{position:absolute;right:75px;top:80px;display:flex;gap:16px;font-size:13px;font-weight:600}
.social span:nth-child(2){color:var(--gold)}
</style>
</head>
<body>

<header class="hero">
  <div class="hero-photo" role="img" aria-label="Golfer wearing a headset swinging in a dark indoor simulator bay with a bright fairway on the screen"></div>
  <nav class="nav">
    <div class="logo"><span class="logo-name">CLEARLINE™</span><span class="logo-sub">BY VESKO GOLF</span></div>
    <div class="nav-links">
      <a class="active" href="#">Home</a><a href="#">Process</a><a href="#">Technology</a><a href="#">The Fit</a><a href="#">Stroke Print</a><a href="#">Testimonials</a><a href="#">About</a>
    </div>
    <a class="btn" href="#">Start My Fitting</a>
  </nav>
  <div class="hero-copy">
    <h1>YOUR SWING.<br>PERFECTED BY AI.</h1>
    <p><strong class="gold">Welcome to Clearline™ by VESKO Golf</strong> — the world’s first fully automated, AI-powered club-fitting system that engineers your perfect bag from data, not guesswork. No appointments. No bias. Just precision built for performance.</p>
    <a class="btn" href="#">Start Your AI Fitting</a>
  </div>
</header>

<section class="welcome">
  <div class="welcome-media" role="img" aria-label="Golfer mid-swing in front of a simulator screen showing swing data"></div>
  <div class="welcome-copy">
    <h2>Welcome to<br>Clearline™ <span class="gold">by VESKO Golf</span></h2>
    <p>Every golfer’s swing is unique — and so should be every club in your bag. Clearline’s AI engine analyzes your swing data, tempo, and ball-flight tendencies, running millions of potential combinations of heads, shafts, and grips across all major OEMs. It isolates the setup that maximizes your distance, consistency, and dispersion — a mathematically optimized build designed for your exact stroke print. From driver to putter, every recommendation is powered by data — not opinion.</p>
    <a class="btn" href="#">Start Your AI Fitting</a>
    <small>No payment required. Receive your personalized Stroke Print Report instantly.</small>
  </div>
</section>

<section class="why">
  <h2>Why Clearline™</h2>
  <p class="sub">AI Fitting Built for Golfers Who Expect Proof</p>
  <div class="why-grid">
    <div class="why-item"><div class="why-icon" role="img" aria-label="AI brain icon"></div><h3>Smarter<br>than human fitting</h3><p>Machine learning,<br>biomechanics, and physics<br>replace guesswork.</p></div>
    <div class="why-item featured"><div class="why-icon" role="img" aria-label="Golf bag icon"></div><h3>Millions of<br>simulations</h3><p>Every major OEM<br>modeled — shafts, lofts, grips,<br>and geometry.</p></div>
    <div class="why-item"><div class="why-icon" role="img" aria-label="Stopwatch icon"></div><h3>Faster than a<br>session</h3><p>Five-minute digital fitting,<br>instant results</p></div>
    <div class="why-item"><div class="why-icon" role="img" aria-label="Report chart icon"></div><h3>Portable<br>confidence</h3><p>Your Stroke Print Report travels<br>with you to any builder.</p></div>
  </div>
</section>

<section class="how">
  <div class="how-card">
    <h2>How It Works</h2>
    <div class="steps">
      <div class="step"><span class="step-num">01</span><div><h3>Input Your Stroke Print</h3><p>Tempo, distances, and goals.</p></div></div>
      <div class="step"><span class="step-num">02</span><div><h3>AI Simulation Engine</h3><p>Tempo, distances, and goals.</p></div></div>
      <div class="step"><span class="step-num">03</span><div><h3>Get Your Report</h3><p>Specs and gapping optimized for your game.</p></div></div>
    </div>
    <a class="btn-outline" href="#">See the Process</a>
    <div class="how-media" role="img" aria-label="Golfer finishing a swing in an indoor simulator bay"></div>
  </div>
  <div class="stat">
    <h2>Designed from 40 Million Swings<br>and Counting</h2>
    <p>Every Clearline fit is backed by real player data, OEM R&amp;D, and physics-based simulation models that calculate the perfect setup for you.</p>
  </div>
</section>

<section class="proof">
  <h2>Proof in<br>Performance</h2>
  <p class="proof-lede">Real Golfers. Real Results. Validated by data.<br>Proven on the course.</p>
  <div class="proof-arrows">
    <svg width="24" height="24" viewBox="0 0 24 24" aria-label="Previous"><circle cx="12" cy="12" r="12" fill="#fff"/><path d="M14 7l-5 5 5 5M9 12h8" stroke="#111" stroke-width="2.2" fill="none" stroke-linecap="round"/></svg>
    <svg width="24" height="24" viewBox="0 0 24 24" aria-label="Next"><circle cx="12" cy="12" r="12" fill="#ffd400"/><path d="M10 7l5 5-5 5M15 12H7" stroke="#111" stroke-width="2.2" fill="none" stroke-linecap="round"/></svg>
  </div>
  <div class="quotes">
    <div class="quote"><blockquote>“Picked up 19 yards on my 7-iron and cut my dispersion in half. Pure data magic.”</blockquote><cite><span class="gold">Marcus L.</span>, 9 Handicap</cite></div>
    <div class="quote"><blockquote>“My Clearline specs matched what my ArcRadar fitter built — but I never left home.”</blockquote><cite><span class="gold">D. Moreno</span>, Scratch Player</cite></div>
    <div class="quote"><blockquote>“It’s like having a Tour-level engineer model your game in real time.”</blockquote><cite><span class="gold">Lena P.</span>, 4 Handicap</cite></div>
  </div>
  <a class="btn-outline" href="#">See All Reviews</a>
</section>

<section class="cta" role="img" aria-label="Dark golf simulator lounge with screens and a hitting mat">
  <div class="cta-overlay"></div>
  <div class="cta-copy">
    <h2>Better Fit. Better Score.<br>Five minutes to a custom AI fit built from your data.</h2>
    <a class="btn" href="#">Start My Clearline Now</a>
  </div>
</section>

<footer class="footer">
  <p class="copy">Copyright © 2025 Company Name All rights reserved.</p>
  <div class="logo"><span class="logo-name">CLEARLINE™</span><span class="logo-sub">BY VESKO GOLF</span></div>
  <p class="tag">Precision Engineered. AI Perfected.</p>
  <div class="social"><span>Feed</span><span>Post</span><span>Photo</span><span>Work</span><span>Video</span></div>
</footer>

</body>
</html>
```